Corporate Branded Documents - IT Provider - On-going work

Hi, I'm Ned a Director of Harbourlane ICT Support a UK Based IT & Telecoms support firm. We've been trading for 12 years now and feel its time for a lick of paint. We have a logo, website etc but would like someone to create some standard documents for us.

- A PDF Proposal Template - We currently don't send our customers proposals as we have nothing that looks good.
- A Quote Template PDF - Example Attached
- A Order Template PDF - Example Attached
- A Invoice Template PDF - Example Attached
- A Generic Document PDF - Something we can use for customer application forms, NDA Agreements, Terms & Conditions etc

Our website can be found at www.harbourlaneictsupport.co.uk - here you'll get a feel for our branding. I've also attached 2 example documents - as well as our currently used documents. Hopefully you guys can see why it needs improving.

We'd also like to work with someone long term, these documents are a start but we'd like to make sure all the work we do looks and feels as smart as possible, so there is plenty of additional work available.

None of these templates need to be Print ready, 99% of the time it will be viewed digitally, so high resolution designs are best

Thanks,

Ned

Target Market(s)

Corporate & Educational Customers

Industry/Entity Type

It Support

Font styles to use
Sans Serif

Colors
ec1f27
0692cd
ffffff

```html
<!DOCTYPE html>
<html lang="en">
<head>
<meta charset="utf-8">
<title>Harbourlane ICT Support – Documents</title>
<link href="https://fonts.googleapis.com/css2?family=Arimo:wght@400;700&family=Tinos:wght@400;700&display=swap" rel="stylesheet">
<style>
:root{
  --red:#d8222a;
  --teal:#127f9a;
  --ink:#1a1a1a;
  --rule:#8f8f8f;
  --soft-rule:#c4c4c4;
  --placeholder:#d9d9d9;
  --paper:#ffffff;
  --backdrop:#d4d4d4;
}
*{box-sizing:border-box;margin:0;padding:0}
html,body{width:1200px;height:852px;overflow:hidden;background:var(--backdrop)}
.stage{width:1326px;height:941px;position:relative;transform:scale(.905);transform-origin:0 0;font-family:"Arimo",Arial,sans-serif;color:var(--ink)}
.page{position:absolute;top:53px;width:597px;height:842px;background:var(--paper);overflow:hidden}
.page--form{left:44px}
.page--nda{left:682px}
.top-bar{position:absolute;top:0;left:0;height:10px;width:505px;background:var(--red)}
.top-bar--teal{left:511px;width:86px;background:var(--teal)}
.brand{position:absolute;top:28px;right:26px;display:flex;align-items:center;gap:5px}
.brand__square{width:19px;height:19px;background:var(--red)}
.brand__name{font-weight:700;font-size:13px;color:var(--teal);width:88px;line-height:13px}
.page-title{position:absolute;left:42px;top:44px;font-size:17px;font-weight:700;color:var(--teal);letter-spacing:.2px}
.page--nda .page-title{left:0;right:0;top:86px;text-align:center}
.intro{position:absolute;left:42px;top:74px;width:515px;font-size:8px;line-height:12px}
.note{position:absolute;left:42px;font-size:7.5px;line-height:10px;padding-left:8px;border-left:3px solid var(--red)}
.date-line{position:absolute;left:411px;top:110px;font-size:10px}
.date-line span,.ph{color:var(--placeholder)}
.section-head{position:absolute;left:42px;width:513px;height:22px;background:var(--teal);color:#fff;font-size:13px;padding:3px 7px}
.grid{position:absolute;left:42px;width:513px;border:1px solid var(--rule);border-top:none}
.row{display:flex;border-bottom:1px solid var(--soft-rule)}
.row:last-child{border-bottom:none}
.row--strong{border-bottom:1px solid var(--rule)}
.cell{flex:1;font-size:7.5px;padding:3px 4px;border-right:1px solid var(--soft-rule);position:relative}
.cell:last-child{border-right:none}
.salute{position:absolute;left:26px;bottom:5px;font-size:7.5px}
.dotted{border-bottom:1px dotted var(--rule)}
.sign{position:absolute;left:42px;top:612px;width:513px;height:64px;display:flex;border-bottom:2px solid var(--rule)}
.sign .cell{border-right:1px solid var(--soft-rule)}
.footer{position:absolute;left:0;bottom:0;width:597px;height:47px;background:var(--teal);display:flex;align-items:center;font-size:8px;color:#fff}
.footer__item{position:absolute;top:18px}
.footer__mark{position:absolute;right:0;top:0;width:44px;height:47px;background:var(--red)}
.legal{position:absolute;left:57px;top:137px;width:465px;font-family:"Tinos","Times New Roman",serif;font-size:11.5px;line-height:15px;text-align:justify}
.legal p{margin-bottom:14px}
.legal .tight{margin-bottom:0}
.clause{display:flex;margin:0 0 14px 20px}
.clause__num{width:38px;flex:none}
.clause u{font-weight:700}
</style>
</head>
<body>
<div class="stage">

  <!-- Registration form -->
  <section class="page page--form">
    <div class="top-bar"></div><div class="top-bar top-bar--teal"></div>
    <div class="brand"><div class="brand__square"></div><div class="brand__name">Harbourlane ICT Support</div></div>
    <h1 class="page-title">CUSTOMER REGISTRATION FORM</h1>
    <p class="intro">Before you complete this form, please read carefully our "Personal Information Protection Policy" and "Conditions of Auction". Please write clearly in block letters.</p>
    <p class="note" style="top:110px">Please fill in either of the categories in which you will participate.</p>
    <div class="date-line">DATE &nbsp;<span>DD</span> / <span>MM</span> / <span>YYYY</span></div>

    <div class="section-head" style="top:128px">Individual Applicant</div>
    <div class="grid" style="top:150px">
      <div class="row" style="height:40px"><div class="cell">Name<span class="salute">Mr. / Ms.</span></div></div>
      <div class="row" style="height:47px">
        <div class="cell" style="flex:0 0 384px;padding:0">
          <div class="dotted" style="height:26px;padding:3px 4px">Home Address</div>
          <div style="display:flex;padding:3px 4px"><span style="width:142px">City/State</span><span style="width:129px">Country</span><span>Postal Code</span></div>
        </div>
        <div class="cell">Date of Birth<div style="margin:10px 0 0 12px;font-size:10px"><span class="ph">DD</span> / <span class="ph">MM</span> / <span class="ph">YYYY</span></div></div>
      </div>
      <div class="row" style="height:21px"><div class="cell" style="flex:0 0 172px">Telephone</div><div class="cell" style="flex:0 0 170px">Mobile</div><div class="cell">Fax</div></div>
      <div class="row" style="height:25px"><div class="cell" style="flex:0 0 256px">Email</div><div class="cell">Occupation</div></div>
    </div>

    <div class="section-head" style="top:295px">Corporate Applicant</div>
    <div class="grid" style="top:317px">
      <div class="row" style="height:40px"><div class="cell">Name of corporation</div></div>
      <div class="row" style="height:40px"><div class="cell">Name of representative<span class="salute">Mr. / Ms.</span></div></div>
      <div class="row" style="height:52px"><div class="cell" style="padding:0">
        <div class="dotted" style="height:26px;padding:3px 4px">Address of corporation</div>
        <div style="display:flex;padding:3px 4px"><span style="width:197px">City/State</span><span style="width:188px">Country</span><span>Postal Code</span></div>
      </div></div>
      <div class="row row--strong" style="height:21px"><div class="cell" style="flex:0 0 256px">Telephone</div><div class="cell">Fax</div></div>
      <div class="row" style="height:40px"><div class="cell">Name of person in charge<span class="salute">Mr. / Ms.</span></div></div>
      <div class="row" style="height:22px"><div class="cell" style="flex:0 0 256px">Department</div><div class="cell">Title</div></div>
      <div class="row" style="height:22px"><div class="cell" style="flex:0 0 256px">Telephone</div><div class="cell">Fax</div></div>
      <div class="row" style="height:22px"><div class="cell" style="flex:0 0 256px">Mobile</div><div class="cell">Email</div></div>
    </div>

    <p class="note" style="top:585px;width:510px">Please read the "Personal Information Protection Policy" on the reverse and sign below after agreeing to the content of that information. If you do not agree, you may not submit an application.</p>
    <div class="sign">
      <div class="cell" style="flex:0 0 193px">Signature of Applicant</div>
      <div class="cell" style="flex:0 0 193px">Print Name(IN BLOCK LETTERS)</div>
      <div class="cell" style="border-right:none">Date<div style="margin:12px 0 0 14px;font-size:10px"><span class="ph">DD</span> / <span class="ph">MM</span> / <span class="ph">YYYY</span></div></div>
    </div>

    <div class="section-head" style="top:687px">Financial Information (for reference only)</div>
    <div class="grid" style="top:709px">
      <div class="row" style="height:19px"><div class="cell" style="flex:0 0 256px">Bank Name</div><div class="cell">Contact<span class="salute" style="left:44px;bottom:1px">Mr. / Ms.</span></div></div>
      <div class="row" style="height:19px"><div class="cell" style="flex:0 0 256px">Telephone / Fax</div><div class="cell">Account Number</div></div>
    </div>

    <footer class="footer">
      <span class="footer__item" style="left:70px">Call Now: 0113 555 0192</span>
      <span class="footer__item" style="left:222px">licensing@harbourlaneictsupport.co.uk</span>
      <span class="footer__item" style="left:408px">www.harbourlaneictsupport.co.uk</span>
      <div class="footer__mark"></div>
    </footer>
  </section>

  <!-- Non-disclosure agreement -->
  <section class="page page--nda">
    <div class="top-bar"></div><div class="top-bar top-bar--teal"></div>
    <div class="brand"><div class="brand__square"></div><div class="brand__name">Harbourlane ICT Support</div></div>
    <h1 class="page-title">NON-DISCLOSURE AGREEMENT</h1>
    <div class="legal">
      <p class="tight">THIS NON-DISCLOSURE AGREEMENT (this "Agreement") is entered into on by &nbsp;&nbsp;&nbsp;&nbsp;&nbsp;&nbsp;&nbsp;&nbsp;&nbsp;&nbsp;&nbsp;&nbsp;&nbsp;&nbsp;&nbsp;&nbsp;&nbsp;&nbsp;&nbsp;&nbsp;&nbsp;&nbsp;&nbsp;&nbsp;&nbsp;&nbsp;&nbsp;&nbsp;&nbsp;&nbsp;&nbsp;&nbsp;&nbsp;&nbsp;&nbsp;&nbsp;&nbsp; and &nbsp;&nbsp;&nbsp;&nbsp;&nbsp;&nbsp;&nbsp;&nbsp;&nbsp;&nbsp;&nbsp;&nbsp;&nbsp;&nbsp;&nbsp;&nbsp;&nbsp;&nbsp;&nbsp;&nbsp;&nbsp;&nbsp;&nbsp;&nbsp;&nbsp;&nbsp;&nbsp;&nbsp;&nbsp;&nbsp;&nbsp;&nbsp;&nbsp;&nbsp;&nbsp; between the undersigned parties on the date specified below.</p>
      <p>WHEREAS, either Party possesses certain confidential proprietary information; and WHEREAS, in connection with the pursuit, evaluation and/or feasibility of a business relationship, and/or the consummation of a transaction (collectively, the "Business Purposes") between the two parties hereto, including their affiliates, subsidiaries, stockholders, partners, co-venture, trading partners, employees and other organizations (hereinafter referred to as Affiliates), confidential proprietary information of one Party may become available to the other Party.</p>
      <p>WHEREAS, either Party desires to prevent the unauthorized use and disclosure of its confidential proprietary information.</p>
      <p>NOW THEREFORE, in consideration of these premises and for other good and valuable consideration, Receipt of which is hereby acknowledged, the parties agree as follows:</p>
      <div class="clause"><span class="clause__num">I.</span><div>"<u>Confidential Information</u>". For purposes of this Agreement, Confidential Information shall mean all strategic and development plans, financial condition, business plans, co-developer identities, data, business records, customer lists, project records, market reports, employee lists and business manuals, policies and procedures, information relating to processes, technologies or theory and all other information which may be disclosed by one Party or to which the other Party may be provided access by the disclosing Party or others in accordance with this Agreement, or which is generated as a result of , incidental to or in connection with the Business Purposes, which is not generally available to the public.</div></div>
      <div class="clause" style="margin-top:28px;margin-bottom:0"><span class="clause__num">II.</span><div><u style="font-weight:700">Non-disclosure Obligations</u>. The Receiving Party promises and agrees to receive and hold the Confidential Information in confidence. Without limiting the generality of the foregoing, the Receiving Party further promises and agrees:</div></div>
      <p class="tight">A. to protect and safeguard the Confidential Information against unauthorized use, publication or disclosure;</p>
      <p class="tight">B. not to use any of the Confidential Information except for the Business Purposes.</p>
      <p class="tight">C. not to, directly or indirectly, in any way, reveal, report, publish, disclose, transfer or otherwise use any of the Confidential Information except as specifically authorized by the Disclosing Party in accordance with this Non-Disclosure Agreement.</p>
      <p class="tight">D. not to use any Confidential Information to unfairly compete or obtain unfair advantage vis-a-vis Disclosing Party in any commercial activity which may be</p>
    </div>
    <footer class="footer">
      <span class="footer__item" style="left:70px">Call Now: 0113 555 0192</span>
      <span class="footer__item" style="left:222px">licensing@harbourlaneictsupport.co.uk</span>
      <span class="footer__item" style="left:408px">www.harbourlaneictsupport.co.uk</span>
      <div class="footer__mark"></div>
    </footer>
  </section>

</div>
</body>
</html>
```